Business Card Design

IT Solutions company.

I need a professional looking design with my company logo if possible.

Logo is located here:
http://www.brunelwavesystems.co.uk/dev/images/logo1.jpg
Feel free to redesign the logo if you think you have any better suggestions.

Our services include, IT Infrastructure/Telephony Maintenance & Hosting Services. Linux and Windows Solutions, App Development.

Out website is currently under development:
http://www.brunelwavesystems.co.uk/dev/

I'm looking for a colourful but professional looking business card.

Industry/Entity Type

Business

Contact Information for Business Card

BW Brunel Wavesystems Ltd
Martin Hollisby
07700958312
www.brunelwavesystems.co.uk
mhollisby@brunelwavesystems.co.uk

```html
<!DOCTYPE html>
<html lang="en">
<head>
<meta charset="utf-8">
<title>Brunel Wavesystems – Business Card</title>
<link href="https://fonts.googleapis.com/css2?family=Exo+2:wght@400;500;700&display=swap" rel="stylesheet">
<style>
  :root {
    --page-bg: #eceae6;
    --card-white: #ffffff;
    --frame-dark: #3b3c40;
    --frame-silver: #c9cbcf;
    --band-dark: #2f3033;
    --band-text: #ffffff;
    --brand-blue: #1f4fa8;
    --text-dark: #2a2b2e;
    --rule: #b9bbbf;
  }
  * { margin: 0; padding: 0; box-sizing: border-box; }
  html, body {
    width: 1200px; height: 677px; overflow: hidden;
    background: var(--page-bg);
    font-family: "Exo 2", sans-serif;
  }
  .stage {
    width: 1200px; height: 677px;
    display: flex; align-items: center; justify-content: center;
  }
  .card {
    width: 356px; height: 610px;
    padding: 9px;
    background: linear-gradient(135deg, var(--frame-dark) 0%, var(--frame-silver) 40%, #f1f2f4 55%, var(--frame-silver) 70%, var(--frame-dark) 100%);
    box-shadow: 0 8px 24px rgba(0,0,0,.18);
  }
  .card-face {
    width: 100%; height: 100%;
    background: var(--card-white);
    display: flex; flex-direction: column;
  }
  .brand {
    height: 150px;
    display: flex; align-items: center; justify-content: center;
    padding-top: 10px;
  }
  .brand-name {
    font-weight: 700; font-size: 21px; color: var(--brand-blue);
    line-height: 1.15; letter-spacing: .3px; text-align: center;
  }
  .name-band {
    background: var(--band-dark);
    color: var(--band-text);
    text-align: center;
    padding: 14px 10px 12px;
    letter-spacing: 1.5px;
  }
  .person-name { font-size: 22px; font-weight: 500; text-transform: uppercase; }
  .person-title { font-size: 16px; font-weight: 400; text-transform: uppercase; margin-top: 2px; }
  .contacts {
    list-style: none;
    padding: 56px 26px 0;
  }
  .contact {
    display: flex; align-items: center; gap: 12px;
    font-size: 13px; color: var(--text-dark);
    margin-bottom: 12px;
  }
  .icon {
    width: 20px; height: 20px; flex: none;
    background: var(--brand-blue); border-radius: 3px;
    display: flex; align-items: center; justify-content: center;
  }
  .icon svg { width: 13px; height: 13px; }
  .rule { border: 0; border-top: 1px solid var(--rule); margin: 8px 16px 14px; }
  .address { padding: 0 26px; }
  .rule-bottom { margin-top: 14px; }
</style>
</head>
<body>
<main class="stage">
  <article class="card">
    <div class="card-face">
      <header class="brand">
        <span class="brand-name">BW Brunel<br>Wavesystems Ltd</span>
      </header>

      <section class="name-band">
        <p class="person-name">Martin Hollisby</p>
        <p class="person-title">General Manager</p>
      </section>

      <ul class="contacts">
        <li class="contact">
          <span class="icon"><svg viewBox="0 0 16 16"><path fill="#fff" d="M4 1.5l2.2 2.8-1.3 1.5c.8 2 2.4 3.6 4.4 4.4l1.5-1.3 2.8 2.2-1.4 2.4C6.8 13.2 2.8 9.2 1.6 3z"/></svg></span>
          <span>07700958312</span>
        </li>
        <li class="contact">
          <span class="icon"><svg viewBox="0 0 16 16"><rect x="4" y="1.5" width="8" height="13" rx="1.5" fill="#fff"/><rect x="5.5" y="3.5" width="5" height="7" fill="#1f4fa8"/></svg></span>
          <span>01632 960418</span>
        </li>
        <li class="contact">
          <span class="icon"><svg viewBox="0 0 16 16"><rect x="1.5" y="3.5" width="13" height="9" fill="#fff"/><path d="M1.5 3.5L8 9l6.5-5.5" fill="none" stroke="#1f4fa8" stroke-width="1.3"/></svg></span>
          <span>mhollisby@brunelwavesystems.co.uk</span>
        </li>
        <li class="contact">
          <span class="icon"><svg viewBox="0 0 16 16"><g fill="none" stroke="#fff" stroke-width="1.3"><circle cx="8" cy="8" r="6"/><ellipse cx="8" cy="8" rx="2.6" ry="6"/><path d="M2 8h12"/></g></svg></span>
          <span>www.brunelwavesystems.co.uk</span>
        </li>
      </ul>

      <hr class="rule">

      <div class="contact address">
        <span class="icon"><svg viewBox="0 0 16 16"><path fill="#fff" d="M8 1a4.5 4.5 0 0 0-4.5 4.5C3.5 9 8 15 8 15s4.5-6 4.5-9.5A4.5 4.5 0 0 0 8 1z"/><circle cx="8" cy="5.5" r="1.7" fill="#1f4fa8"/></svg></span>
        <span>42 Harbour Lane, Bristol, UK</span>
      </div>

      <hr class="rule rule-bottom">
    </div>
  </article>
</main>
</body>
</html>
```